Crestline Staffing PEO - Web Build for Professional Employment Organization

We need a website built for our new PEO (professional employment organization). This company will offer third party Human Resource services to companies who are looking to outsource:<br/>Recruiting<br/>Administrative Onboarding<br/>New hire training, ongoing training and development<br/>Payroll/compensation processing/services<br/>Employee Relations<br/>Unemployment Claim Facilitation<br/>Benefits Plans and Administration<br/><br/>I have attached the logo below. Please use that as a reference and color match as best as possible. <br/><br/>Here are some of the competitor's websites:<br/>https://www.velmorahr.com/ <br/>https://www.trundelpay.com/<br/>https://www.trundelpay.com/<br/>https://www.qzn.com/<br/>https://www.bremwickhr.com/<br/>https://orvalepeo.com/contact-orvale/<br/><br/>

Target Market(s)

Startups and mid-sized businesses

Number of Pages Required

5+ page

Font styles to use
Sans Serif

Colors
0592cd

Requirements
Must have
• Features Pages
• SEO driven keyword rich content
• Strong focus on our ability to provide unemployment claim facilitation services as well as mandatory training/certification fulfillment
Nice to have
• I'd like to see one mockup with a Live Chat version if possible. In theory, the Live Chat messages would go directly to our front desk person.

```html
<!DOCTYPE html>
<html lang="en">
<head>
<meta charset="utf-8">
<title>Crestline Staffing PEO</title>
<link rel="stylesheet" href="https://fonts.googleapis.com/css2?family=Montserrat:wght@400;500;600&family=Signika:wght@400;500;600&display=swap">
<style>
:root{
  --blue:#0592cd;
  --blue-deep:#0b6fbf;
  --slate:#3e4a5e;
  --ink:#333;
  --muted:#666;
  --line:#d9d9d9;
  --paper:#fff;
  --soft:#f1f1f1;
  --dark:#343434;
}
*{box-sizing:border-box;margin:0;padding:0}
html,body{width:1200px;height:3715px;overflow:hidden}
body{position:relative;background:var(--paper);font-family:"Montserrat",sans-serif;color:var(--ink)}
.abs{position:absolute}

/* header */
.site-header{position:absolute;left:0;top:0;width:1200px;height:130px;background:var(--paper);box-shadow:0 2px 6px rgba(0,0,0,.08);z-index:5}
.brand{position:absolute;left:111px;top:38px;width:314px;text-align:left;font-family:"Signika",sans-serif;font-weight:600;font-size:32px;color:var(--slate);letter-spacing:1px;line-height:1;white-space:nowrap}
.brand-sub{position:absolute;left:111px;top:76px;font-family:"Signika",sans-serif;font-weight:600;font-size:18px;color:var(--slate);letter-spacing:14px;width:314px;text-align:center}
.contact-bar{position:absolute;left:640px;top:0;width:560px;height:52px}
.contact-item{position:absolute;top:12px;color:#fff;font-weight:600;display:flex;align-items:center;gap:8px}
.nav{position:absolute;top:84px;left:487px;display:flex;font-size:16px;font-weight:500;color:var(--ink)}
.nav a{color:inherit;text-decoration:none;padding:6px 9px;margin-right:9px;border-radius:14px;white-space:nowrap}
.nav a:last-child{margin-right:0}
.nav a.active{background:var(--blue);color:#fff}

/* hero */
.hero{position:absolute;left:0;top:130px;width:1200px;height:617px;background:linear-gradient(90deg,#f2f3f5,#e3e6ea 60%,#dadfe4);overflow:hidden}
.hero-photo{position:absolute;left:690px;top:30px;width:380px;height:560px;background:linear-gradient(180deg,#d8c7b3 0%,#2d2d30 55%,#1c1c1e 100%);border-radius:190px 190px 0 0;opacity:.85}
.hero-title{position:absolute;left:111px;top:108px;font-family:"Signika",sans-serif;font-weight:600;font-size:56px;color:var(--slate);letter-spacing:2px;white-space:nowrap}
.hero-sub{position:absolute;left:111px;top:198px;font-family:"Signika",sans-serif;font-size:32px;color:#222;white-space:nowrap}
.btn{position:absolute;font-family:"Signika",sans-serif;font-weight:500;font-size:19px;border-radius:10px;display:flex;align-items:center;justify-content:center}
.btn-dark{background:var(--slate);color:#fff}
.btn-outline{border:2px solid #fff;color:#fff}
.arrow{position:absolute;width:28px;height:48px}

/* sections */
.section-title{position:absolute;left:0;width:1200px;text-align:center;font-family:"Signika",sans-serif;font-weight:500;font-size:40px;color:var(--blue)}
.section-lead{position:absolute;left:140px;width:920px;text-align:center;font-size:15px;line-height:27px;color:#444}
.service{position:absolute;width:300px;text-align:center}
.service-icon{width:110px;height:110px;border-radius:50%;margin:0 auto;background:#3f3f3f;display:flex;align-items:center;justify-content:center}
.service-icon.is-featured{background:var(--blue)}
.service h3{font-family:"Signika",sans-serif;font-weight:500;font-size:20px;margin-top:22px;color:#333;white-space:nowrap}
.service h3.is-featured{color:var(--blue)}
.service p{font-size:14.5px;line-height:24px;color:#666;margin:6px auto 0;width:285px}

.claim{position:absolute;left:0;top:1294px;width:1200px;height:468px;background:linear-gradient(90deg,#dfe3e8,#eceef1)}
.claim-photo{position:absolute;left:765px;top:34px;width:390px;height:382px;background:linear-gradient(135deg,#c9d2da 0%,#b7c3cd 40%,#c98a84 70%,#e4e7eb 100%);opacity:.8}
.claim-title{position:absolute;left:111px;top:118px;font-family:"Signika",sans-serif;font-weight:500;font-size:32px;color:#fff;white-space:nowrap}
.claim-text{position:absolute;left:111px;top:166px;width:570px;font-size:15px;line-height:26px;color:#fff}

.team-card{position:absolute;background:#fff;border:1px solid var(--line);text-align:center}
.team-photo{position:absolute;left:50%;transform:translateX(-50%);width:170px;background:linear-gradient(180deg,#e6d6c8 0%,#3a3a3e 45%,#2a2a2e 100%);border-radius:80px 80px 0 0}
.team-name{position:absolute;left:0;width:100%;font-family:"Signika",sans-serif;font-weight:500;font-size:25px;color:#222}
.team-text{position:absolute;left:0;width:100%;font-size:14.5px;line-height:24px;color:#666}

.testimonials{position:absolute;left:0;top:2618px;width:1200px;height:743px;background:var(--soft)}
.quote-card{position:absolute;background:#fff;border:1px solid var(--line);width:450px;height:293px;text-align:center}
.quote-card p{position:absolute;left:28px;width:394px;top:180px;font-size:13px;line-height:21px;color:#444}
.quote-card cite{position:absolute;left:0;width:100%;top:254px;font-style:normal;font-size:13px;color:var(--blue)}

.site-footer{position:absolute;left:0;top:3240px;width:1200px;height:475px}
.footer-brand{position:absolute;left:111px;top:212px;width:391px;text-align:center;font-family:"Signika",sans-serif;font-weight:600;font-size:40px;color:#fff;letter-spacing:1px;white-space:nowrap}
.footer-brand-sub{position:absolute;left:111px;top:262px;width:391px;text-align:center;font-family:"Signika",sans-serif;font-weight:600;font-size:22px;color:#fff;letter-spacing:16px}
.footer-head{position:absolute;top:142px;font-family:"Signika",sans-serif;font-weight:600;font-size:19px;color:#fff;letter-spacing:-.3px}
.footer-links{position:absolute;left:594px;top:196px;list-style:none;color:#fff;font-size:15px}
.footer-links li{height:33.5px;display:flex;align-items:center;gap:14px}
.footer-links li::before{content:"";width:8px;height:8px;border-radius:50%;background:#fff}
.footer-contact{position:absolute;left:828px;top:196px;color:#fff;font-size:15px;line-height:20px}
.footer-contact div{position:absolute;left:0;display:flex;gap:14px;align-items:flex-start;width:300px}
.footer-rule{position:absolute;left:111px;top:386px;width:976px;height:1px;background:#ddd}
.copyright{position:absolute;left:0;width:1200px;top:422px;text-align:center;font-family:"Signika",sans-serif;font-weight:500;font-size:17px;color:#fff}
</style>
</head>
<body>

<header class="site-header">
  <div class="brand">CRESTLINE STAFFING</div>
  <div class="brand-sub">PEO</div>
  <svg class="contact-bar" viewBox="0 0 560 52" aria-hidden="true"><polygon points="0,0 560,0 560,52 50,52" fill="#0592cd"/></svg>
  <span class="contact-item" style="left:700px;font-size:15px">
    <svg width="26" height="26" viewBox="0 0 26 26"><circle cx="13" cy="13" r="12" fill="none" stroke="#fff" stroke-width="1.6"/><rect x="7" y="9" width="12" height="8" fill="none" stroke="#fff" stroke-width="1.4"/><polyline points="7,9 13,14 19,9" fill="none" stroke="#fff" stroke-width="1.4"/></svg>contact@company.com</span>
  <span class="contact-item" style="left:953px;font-size:14px">
    <svg width="26" height="26" viewBox="0 0 26 26"><circle cx="13" cy="13" r="12" fill="none" stroke="#fff" stroke-width="1.6"/><path d="M9 7c-1 1-1 3 1 6s5 5 6 5 2-1 2-2l-2-2-2 1c-1-1-2-2-3-4l1-2z" fill="#fff"/></svg>+123 456 7890</span>
  <nav class="nav">
    <a class="active">HOME</a><a>ABOUT</a><a>SERVICES</a><a>BLOG</a><a>TESTIMONIAL</a><a>CONTACT US</a>
  </nav>
</header>

<section class="hero">
  <div class="hero-photo" role="img" aria-label="Photo of a smiling businesswoman holding a notepad"></div>
  <svg class="abs" style="left:0;top:420px" width="1200" height="197" viewBox="0 0 1200 197" aria-hidden="true">
    <polygon points="0,135 600,197 1200,0 1200,80 600,197 0,90" fill="#0b6fbf" opacity=".9"/>
    <polygon points="0,135 0,97 600,197" fill="#0592cd"/>
    <polygon points="600,197 1200,40 1200,95" fill="#0592cd"/>
  </svg>
  <div class="hero-title">CRESTLINE STAFFING</div>
  <div class="hero-sub">Professional Employment Organization</div>
  <div class="btn btn-dark" style="left:111px;top:265px;width:117px;height:61px">Read More</div>
  <svg class="arrow" style="left:43px;top:204px" viewBox="0 0 28 48"><polyline points="24,4 4,24 24,44" fill="none" stroke="#555" stroke-width="2.5"/></svg>
  <svg class="arrow" style="left:1131px;top:204px" viewBox="0 0 28 48"><polyline points="4,4 24,24 4,44" fill="none" stroke="#555" stroke-width="2.5"/></svg>
</section>

<h2 class="section-title" style="top:837px">Human Resource Services</h2>
<p class="section-lead" style="top:894px;font-size:17px">to companies who are looking to outsource</p>
<svg class="arrow" style="left:40px;top:1080px" viewBox="0 0 28 48"><polyline points="24,4 4,24 24,44" fill="none" stroke="#555" stroke-width="2.5"/></svg>
<svg class="arrow" style="left:1122px;top:1080px" viewBox="0 0 28 48"><polyline points="4,4 24,24 4,44" fill="none" stroke="#555" stroke-width="2.5"/></svg>

<div class="service" style="left:105px;top:969px">
  <div class="service-icon"><svg width="56" height="56" viewBox="0 0 56 56" fill="#fff"><circle cx="28" cy="24" r="8"/><path d="M14 46c0-9 6-14 14-14s14 5 14 14z"/><circle cx="12" cy="28" r="5"/><circle cx="44" cy="28" r="5"/></svg></div>
  <h3>RECRUITING</h3>
  <p>Sed ut perspiciatis unde omnis iste natus error sit voluptatem accusantium omnis iste</p>
</div>
<div class="service" style="left:450px;top:969px">
  <div class="service-icon is-featured"><svg width="60" height="60" viewBox="0 0 60 60" fill="none" stroke="#fff" stroke-width="2.5"><circle cx="30" cy="30" r="20"/><line x1="30" y1="4" x2="30" y2="14"/><line x1="30" y1="46" x2="30" y2="56"/><line x1="4" y1="30" x2="14" y2="30"/><line x1="46" y1="30" x2="56" y2="30"/><circle cx="30" cy="26" r="6" fill="#fff"/><path d="M20 42c2-6 18-6 20 0" fill="#fff"/></svg></div>
  <h3 class="is-featured">ADMINISTRATIVE ONBOARDING</h3>
  <p>Sed ut perspiciatis unde omnis iste natus error sit voluptatem accusantium omnis iste</p>
</div>
<div class="service" style="left:798px;top:969px">
  <div class="service-icon"><svg width="56" height="56" viewBox="0 0 56 56" fill="#fff"><rect x="20" y="10" width="16" height="12" rx="1"/><rect x="12" y="26" width="32" height="5"/><circle cx="10" cy="22" r="4"/><circle cx="46" cy="22" r="4"/><rect x="6" y="28" width="6" height="16"/><rect x="44" y="28" width="6" height="16"/><rect x="16" y="31" width="4" height="13"/><rect x="36" y="31" width="4" height="13"/></svg></div>
  <h3>EMPLOYEE RELATIONS</h3>
  <p>Sed ut perspiciatis unde omnis iste natus error sit voluptatem accusantium omnis iste</p>
</div>

<section class="claim">
  <div class="claim-photo" role="img" aria-label="Overhead photo of a team meeting around a glass table"></div>
  <svg class="abs" style="left:0;top:63px" width="800" height="342" viewBox="0 0 800 342" aria-hidden="true"><polygon points="0,0 692,0 793,171 692,342 0,342" fill="#0b6fbf"/></svg>
  <h2 class="claim-title">Unemployment Claim Facilitation Services</h2>
  <p class="claim-text">Nemo enim ipsam voluptatem quia voluptas sit aspernatur aut odit aut fugit, sed quia consequuntur magni dolores eos qui ratione voluptatem quia voluptas sit aspernatur aut odit aut fugit, sed quia consequuntur magni dolores.</p>
  <div class="btn btn-outline" style="left:111px;top:293px;width:117px;height:59px">Read More</div>
</section>

<h2 class="section-title" style="top:1845px">Meet Our Team</h2>
<p class="section-lead" style="top:1911px">Nemo enim ipsam voluptatem quia voluptas sit aspernatur aut odit aut fugit, sed quia consequuntur magni dolores eos qui ratione voluptatem</p>
<svg class="arrow" style="left:43px;top:2247px" viewBox="0 0 28 48"><polyline points="24,4 4,24 24,44" fill="none" stroke="#555" stroke-width="2.5"/></svg>
<svg class="arrow" style="left:1131px;top:2247px" viewBox="0 0 28 48"><polyline points="4,4 24,24 4,44" fill="none" stroke="#555" stroke-width="2.5"/></svg>

<div class="team-card" style="left:112px;top:2045px;width:303px;height:450px">
  <div class="team-photo" role="img" aria-label="Portrait of team member Clara Smith" style="top:24px;height:250px"></div>
  <svg class="abs" style="left:15px;top:235px" width="273" height="74" viewBox="0 0 273 74"><polygon points="0,0 136,50 273,0 273,24 136,74 0,24" fill="#3a3a3a"/></svg>
  <div class="team-name" style="top:333px">Clara Smith</div>
  <div class="team-text" style="top:377px">Sed ut perspiciatis unde omnis iste<br>natus error sit voluptatem</div>
</div>
<div class="team-card" style="left:436px;top:2026px;width:328px;height:491px;box-shadow:0 0 6px rgba(0,0,0,.06)">
  <div class="team-photo" role="img" aria-label="Portrait of team member Jhon Doe" style="top:34px;height:258px"></div>
  <svg class="abs" style="left:15px;top:257px" width="296" height="80" viewBox="0 0 296 80"><polygon points="0,0 148,54 296,0 296,26 148,80 0,26" fill="#0592cd"/></svg>
  <div class="team-name" style="top:360px;color:var(--blue)">Jhon Doe</div>
  <div class="team-text" style="top:408px;font-size:16px;line-height:26px">Sed ut perspiciatis unde omnis iste<br>natus error sit voluptatem</div>
</div>
<div class="team-card" style="left:783px;top:2045px;width:304px;height:450px">
  <div class="team-photo" role="img" aria-label="Portrait of team member Anne Smith" style="top:24px;height:250px"></div>
  <svg class="abs" style="left:15px;top:235px" width="273" height="74" viewBox="0 0 273 74"><polygon points="0,0 136,50 273,0 273,24 136,74 0,24" fill="#3a3a3a"/></svg>
  <div class="team-name" style="top:333px">Anne Smith</div>
  <div class="team-text" style="top:377px">Sed ut perspiciatis unde omnis iste<br>natus error sit voluptatem</div>
</div>

<section class="testimonials">
  <h2 class="section-title" style="top:65px">Our Testimonials</h2>
  <p class="section-lead" style="top:130px">Nemo enim ipsam voluptatem quia voluptas sit aspernatur aut odit aut fugit, sed quia consequuntur magni dolores eos qui ratione voluptatem</p>
  <svg class="arrow" style="left:43px;top:361px" viewBox="0 0 28 48"><polyline points="24,4 4,24 24,44" fill="none" stroke="#555" stroke-width="2.5"/></svg>
  <svg class="arrow" style="left:1131px;top:361px" viewBox="0 0 28 48"><polyline points="4,4 24,24 4,44" fill="none" stroke="#555" stroke-width="2.5"/></svg>
  <div class="quote-card" style="left:130px;top:238px">
    <svg class="abs" style="left:115px;top:38px" width="220" height="112" viewBox="0 0 220 112"><polygon points="0,54 110,92 220,54 220,76 110,112 0,76" fill="#3a3a3a"/><circle cx="110" cy="45" r="45" fill="#0592cd"/><text x="110" y="78" text-anchor="middle" font-family="Signika,sans-serif" font-weight="600" font-size="72" fill="#fff">“</text></svg>
    <p>Nemo enim ipsam voluptatem quia voluptas sit aspernatur aut odit aut fugit, sed quia consequuntur magni dolores eos qui ratione voluptatem.</p>
    <cite>- Thompson</cite>
  </div>
  <div class="quote-card" style="left:620px;top:238px">
    <svg class="abs" style="left:115px;top:38px" width="220" height="112" viewBox="0 0 220 112"><polygon points="0,54 110,92 220,54 220,76 110,112 0,76" fill="#3a3a3a"/><circle cx="110" cy="45" r="45" fill="#0592cd"/><text x="110" y="78" text-anchor="middle" font-family="Signika,sans-serif" font-weight="600" font-size="72" fill="#fff">“</text></svg>
    <p>Nemo enim ipsam voluptatem quia voluptas sit aspernatur aut odit aut fugit, sed quia consequuntur magni dolores eos qui ratione voluptatem.</p>
    <cite>- Thompson</cite>
  </div>
</section>

<footer class="site-footer">
  <svg class="abs" style="left:0;top:0" width="1200" height="475" viewBox="0 0 1200 475" aria-hidden="true">
    <polygon points="0,100 600,0 1200,100 1200,475 0,475" fill="#0592cd"/>
    <polygon points="0,121 600,22 1200,121 1200,475 0,475" fill="#343434"/>
  </svg>
  <div class="footer-brand">CRESTLINE STAFFING</div>
  <div class="footer-brand-sub">PEO</div>
  <div class="footer-head" style="left:588px">QUICK LINKS</div>
  <ul class="footer-links"><li>Home</li><li>About</li><li>Articles</li><li>Testimonials</li></ul>
  <div class="footer-head" style="left:828px">CONTACT US</div>
  <div class="footer-contact">
    <div style="top:0"><svg width="32" height="32" viewBox="0 0 32 32" fill="none" stroke="#fff" stroke-width="1.4"><circle cx="16" cy="16" r="15"/><path d="M16 24s-6-6-6-10a6 6 0 0 1 12 0c0 4-6 10-6 10z"/><circle cx="16" cy="14" r="2"/></svg><span style="padding-top:2px">123 Sky Tower, West 21th Street,<br>Suite, US</span></div>
    <div style="top:58px"><svg width="32" height="32" viewBox="0 0 32 32" fill="none" stroke="#fff" stroke-width="1.4"><circle cx="16" cy="16" r="15"/><rect x="9" y="11" width="14" height="10"/><polyline points="9,11 16,17 23,11"/></svg><span style="padding-top:8px">contact@company.com</span></div>
    <div style="top:112px"><svg width="32" height="32" viewBox="0 0 32 32" fill="none" stroke="#fff" stroke-width="1.4"><circle cx="16" cy="16" r="15"/><path d="M11 9c-1 1-1 4 2 8s6 6 8 6c1 0 2-1 2-2l-3-3-2 1c-1-1-3-3-4-5l1-2z"/></svg><span style="padding-top:8px">+123 456 7890</span></div>
  </div>
  <div class="footer-rule"></div>
  <div class="copyright">Copyrights @ 2020 Crestline Staffing. All Rights Reserved.</div>
</footer>

</body>
</html>
```